Sunset Harbor Living Web Page

We need a web page design that has two intro pages - first being a 'home page', then a link to the second page that has the 'content tabs' and a 'call to action' (see below).

The business helps people that wish to retire to S.E.Asia (Thailand, Malaysia, Indonesia,The Philippines etc) - to enjoy the lifestyle and the remaining years of their lives. What attracts S.E.Asia to many people is the lower cost, the atmoshpere and beauty of the tropics and the vibrancy of the various countries.

People that are wishing to make the most of their retirement and are adventurous at a great bargain compared to the cost of their own countries will be interested.

We help them achieve this - visa, financials (tax, gov't payments etc), introduce them to the right people for property, clubs, retirement facilities, insurance and so forth.

Therefore we are providing an extremely wide ranging service and this site will provide broad but general information only - with a call to action to come and see us for more specific information and how we can help them specifically.

This site will be predominantly for travel and lifestyle, it will be linked with another financial services (financial planning) site later down the track.

The colour scheme is dark green and blue - as per the attached logo design. Photos and background just think lifestyle and S.E.Asia - beaches/mountains/water/recreational activities for retirees.

Target market is mostly those coming up to retirement to those that are already retired. But we also expect to have some interest with younger people that would like to find out more and plan for the future. So a broad age group but I would say mostly 40-70 yrs old.

On the first (Home) page we would like our company name 'Sunset Harbor Living', our logo (which will be on all pages) and a statement such as: “Imagine a retirement where your dreams are brought to life, and you have never felt more alive. Let us show you how”. Then a link to the second page.

We would like an uncluttered site. On the second (contents) page the tabs would be:

- Visa
- Property
- Financials
- Travel
- Insurance & Healthcare
- Medical Tourism
- Cost of living
- Weekly Blogs and articles
- Sunset Harbor Living story

We would also like a call to action on the second page - asking them to leave their contact details if they wish to learn more or sign up to our weekly newsletter/blog.

We are open to suggestions and your imaginations.

Thank you
Malcolm

Font styles to use
Serif
Script

Colors
0255a3
3377b5
00a990
9bcb3c
abd036
33b8a4
85abd2
cadf82
86cfc6

Requirements
Must have
• I have been asked by the web designer to receive a 'Web Font' so that we can 'get off of Zentrofy'. Hope that makes sense.

```html
<!DOCTYPE html>
<html lang="en">
<head>
<meta charset="utf-8">
<title>Sunset Harbor Living — Home</title>
<link rel="stylesheet" href="https://fonts.googleapis.com/css2?family=Lato:wght@700;900&family=Yesteryear&display=swap">
<style>
  :root {
    --sky-top: #2e3f50;
    --sky-low: #3d5366;
    --horizon: #5a6470;
    --sand-dark: #8d7e6c;
    --sand-light: #b8a58c;
    --brand-green: #00b050;
    --brand-blue: #1da3e0;
    --script-blue: #27a9e8;
    --white: #ffffff;
    --tagline: #f2f2f2;
  }
  * { margin: 0; padding: 0; box-sizing: border-box; }
  html, body { width: 1200px; height: 683px; overflow: hidden; background: var(--sky-top); }
  .home-hero {
    position: relative;
    width: 1200px;
    height: 683px;
    overflow: hidden;
    font-family: "Lato", Arial, sans-serif;
  }
  .hero-backdrop {
    position: absolute;
    inset: 0;
    background:
      linear-gradient(180deg, rgba(20,32,44,0.35) 0%, rgba(20,32,44,0.15) 60%, rgba(20,32,44,0.25) 100%),
      linear-gradient(180deg, var(--sky-top) 0%, var(--sky-low) 45%, var(--horizon) 55%, var(--sand-dark) 64%, var(--sand-light) 100%);
  }
  .brand {
    position: absolute;
    left: 0;
    right: 0;
    top: 160px;
    display: flex;
    flex-direction: column;
    align-items: center;
  }
  .brand-mark {
    width: 118px;
    height: 118px;
    border-radius: 50%;
    background: var(--brand-green);
    margin-bottom: 20px;
  }
  .brand-name {
    font-weight: 700;
    font-size: 32px;
    line-height: 1;
    color: var(--white);
    letter-spacing: -0.3px;
  }
  .brand-tagline {
    margin-top: 6px;
    font-weight: 900;
    font-size: 11.5px;
    letter-spacing: 0.4px;
    color: var(--tagline);
    text-transform: uppercase;
  }
  .hero-statement {
    position: absolute;
    left: 0;
    right: 0;
    top: 366px;
    text-align: center;
    font-family: "Yesteryear", cursive;
    font-size: 31px;
    line-height: 48px;
    color: var(--script-blue);
    text-shadow: 0 0 6px rgba(0,0,0,0.55), 0 0 2px rgba(0,0,0,0.6);
  }
  .cta-button {
    position: absolute;
    left: 438px;
    top: 494px;
    width: 334px;
    height: 55px;
    display: flex;
    align-items: center;
    border: 2px solid var(--white);
    border-radius: 5px;
    background: var(--brand-green);
    overflow: hidden;
    text-decoration: none;
  }
  .cta-label {
    flex: 1;
    padding-left: 21px;
    font-weight: 700;
    font-size: 20px;
    letter-spacing: 0.2px;
    color: var(--white);
  }
  .cta-arrow {
    position: relative;
    width: 62px;
    height: 100%;
  }
  .cta-arrow svg { position: absolute; inset: 0; width: 100%; height: 100%; }
</style>
</head>
<body>
  <main class="home-hero">
    <div class="hero-backdrop" role="img" aria-label="Photo of a laughing retired couple running hand in hand across sunny beach sand dunes, under a dark blue overlay"></div>

    <header class="brand">
      <div class="brand-mark" aria-hidden="true"></div>
      <h1 class="brand-name">Sunset Harbor Living</h1>
      <p class="brand-tagline">Dream Lifestyle Specialists</p>
    </header>

    <p class="hero-statement">Imagine A Retirement Where Your Dreams Are Brought To Life,<br>&amp; You Have Never Felt More Alive</p>

    <a class="cta-button" href="#contents">
      <span class="cta-label">LET US SHOW YOU HOW</span>
      <span class="cta-arrow" aria-hidden="true">
        <svg viewBox="0 0 62 51" preserveAspectRatio="none">
          <path d="M12 0 H62 V51 H12 A30 26 0 0 1 12 0 Z" fill="var(--brand-blue)"/>
          <path d="M12 0 A30 26 0 0 0 12 51" fill="none" stroke="var(--white)" stroke-width="2.5"/>
          <path d="M25 16 L34 25.5 L25 35 M33 16 L42 25.5 L33 35" fill="none" stroke="var(--white)" stroke-width="2"/>
        </svg>
      </span>
    </a>
  </main>
</body>
</html>
```